SkyvornQ Business Cards and Stationary Design

Need a design for our business cards and stationary. I want to carry on the theme of the logo. I want the business cards to have a design on the back. I would like the business cards and the stationary to carry the same theme, design scheme, and branding

Target Market(s)

Airlines and Maintenance Facilities

Industry/Entity Type

Aviation

Contact Information for Business Card

Name
Position Title
Address: 4827 Trellis Hollow Road, Fort Pierce, Florida, 34951
Office Number
Mobile Number
Email
Website

Font styles to use
Serif
Sans Serif

Colors

Designer to choose colors to be used in the design.

```html
<!DOCTYPE html>
<html lang="en">
<head>
<meta charset="UTF-8">
<title>SkyvornQ Business Card</title>
<link href="https://fonts.googleapis.com/css2?family=Open+Sans:wght@400;600;700;800&display=swap" rel="stylesheet">
<style>
  :root {
    --navy: #03175a;
    --navy-deep: #021556;
    --navy-soft: #0a2478;
    --blue: #1f3fd0;
    --ink: #333333;
    --white: #ffffff;
    --bg-light: #e8e8e8;
    --bg-dark: #c8c8c8;
    --edge: #1a1a1a;
  }
  * { margin: 0; padding: 0; box-sizing: border-box; }
  html, body { width: 1200px; height: 1141px; overflow: hidden; }
  body {
    position: relative;
    background: linear-gradient(135deg, var(--bg-light) 0%, var(--bg-dark) 100%);
    font-family: "Open Sans", Arial, sans-serif;
  }
  .card {
    position: absolute;
    width: 847px;
    height: 484px;
    background: var(--white);
    border: 1.5px solid var(--edge);
    border-radius: 46px;
    overflow: hidden;
  }
  .card--front { left: 76px; top: 69px; }
  .card--back { left: 279px; top: 596px; }

  .footer-band {
    position: absolute; left: 0; top: 350px;
    width: 847px; height: 134px;
    background: linear-gradient(180deg, var(--navy-soft) 0%, var(--navy-deep) 60%);
  }

  .brand-ring {
    position: absolute;
    border-radius: 50%;
    border-style: solid;
    border-color: var(--blue);
  }
  .brand-name {
    position: absolute;
    font-weight: 800;
    color: var(--navy);
    white-space: nowrap;
    line-height: 1;
    text-align: center;
  }
  .card--front .brand-ring { left: 197px; top: 92px; width: 112px; height: 112px; border-width: 9px; }
  .card--front .brand-name {
    left: 55px; top: 230px; width: 400px;
    font-size: 42px; letter-spacing: 0.3em; padding-left: 0.3em;
  }

  .divider {
    position: absolute; left: 474px; top: 82px;
    width: 3px; height: 206px; background: #c9c9c9;
  }
  .person-name {
    position: absolute; left: 503px; top: 83px;
    font-size: 28px; font-weight: 700; color: var(--navy);
    letter-spacing: 0.01em;
  }
  .person-title {
    position: absolute; left: 503px; top: 120px;
    font-size: 24px; font-weight: 400; color: var(--ink);
    letter-spacing: 0.03em;
  }
  .contact-list { position: absolute; left: 502px; top: 166px; list-style: none; }
  .contact-list li {
    display: flex; align-items: center; gap: 6px;
    height: 30px; font-size: 18.5px; color: #222;
  }
  .contact-list svg { width: 19px; height: 19px; flex: none; }

  .address {
    position: absolute; left: 0; top: 438px; width: 847px;
    display: flex; justify-content: center; align-items: center; gap: 7px;
    font-size: 18px; color: var(--white);
  }
  .address svg { width: 17px; height: 17px; }

  .card--back .brand-ring { left: 347px; top: 102px; width: 152px; height: 152px; border-width: 12px; }
  .card--back .brand-name {
    left: 0; top: 282px; width: 847px;
    font-size: 52px; letter-spacing: 0.4em; padding-left: 0.4em;
  }
  .back-url {
    position: absolute; left: 0; top: 400px; width: 847px;
    text-align: center; font-size: 25px; color: #222;
    letter-spacing: 0.2em; padding-left: 0.2em;
  }
</style>
</head>
<body>

<section class="card card--front">
  <div class="footer-band" role="img" aria-label="Navy footer band with blue accent lines"></div>

  <div class="brand-ring"></div>
  <div class="brand-name">SKYVORNQ</div>

  <div class="divider"></div>
  <h1 class="person-name">MARCUS DELHAVEN</h1>
  <p class="person-title">PRESIDENT</p>

  <ul class="contact-list">
    <li>
      <svg viewBox="0 0 20 20"><circle cx="10" cy="10" r="8.6" fill="none" stroke="var(--navy)" stroke-width="1.4"/><path d="M7 5.5l1.6 2.4-1 1.2c.6 1.3 1.6 2.3 2.9 2.9l1.2-1 2.4 1.6-.8 1.6c-3.8-.3-7-3.5-7.3-7.3z" fill="var(--navy)"/></svg>
      012-345-6789
    </li>
    <li>
      <svg viewBox="0 0 20 20"><circle cx="10" cy="10" r="8.6" fill="none" stroke="var(--navy)" stroke-width="1.4"/><rect x="7" y="5" width="6" height="10" rx="1" fill="none" stroke="var(--navy)" stroke-width="1.3"/><circle cx="10" cy="13" r=".8" fill="var(--navy)"/></svg>
      012-345-6789
    </li>
    <li>
      <svg viewBox="0 0 20 20"><circle cx="10" cy="10" r="8.6" fill="none" stroke="var(--navy)" stroke-width="1.4"/><rect x="5.5" y="7" width="9" height="6.5" fill="none" stroke="var(--navy)" stroke-width="1.3"/><path d="M5.5 7l4.5 3.5L14.5 7" fill="none" stroke="var(--navy)" stroke-width="1.3"/></svg>
      info@skyvornq.com
    </li>
    <li>
      <svg viewBox="0 0 20 20"><circle cx="10" cy="10" r="8.6" fill="none" stroke="var(--navy)" stroke-width="1.4"/><ellipse cx="10" cy="10" rx="3.6" ry="8.6" fill="none" stroke="var(--navy)" stroke-width="1.2"/><path d="M1.5 10h17M3 6h14M3 14h14" stroke="var(--navy)" stroke-width="1.2"/></svg>
      www.skyvornq.com
    </li>
  </ul>

  <p class="address">
    <svg viewBox="0 0 20 20"><circle cx="10" cy="10" r="8.6" fill="none" stroke="var(--white)" stroke-width="1.5"/><path d="M10 4.5a3.5 3.5 0 0 1 3.5 3.5c0 2.6-3.5 6.5-3.5 6.5S6.5 10.6 6.5 8A3.5 3.5 0 0 1 10 4.5z" fill="none" stroke="var(--white)" stroke-width="1.3"/><circle cx="10" cy="8" r="1.2" fill="var(--white)"/></svg>
    4827 Trellis Hollow Road, Fort Pierce, Florida, 34951
  </p>
</section>

<section class="card card--back">
  <div class="brand-ring"></div>
  <div class="brand-name">SKYVORNQ</div>
  <p class="back-url">www.skyvornq.com</p>
</section>

</body>
</html>
```